Gravelstern Rum Liqueur Bottle Label

I will be launching a Rum Liqueur called Gravelstern Spiced Rum Liqueur. The bottle I have chosen to use is an KVT 500ml type and I have included a photo of it in the project brief. The bottle dimensions are height 193.5mm with diameter 85mm. There will be a cork closure, sealed with a heat shrink capsule. I require two labels for each bottle, a large rectangular label on the front with the product name, logo, label design and the bottle quantity which is 500ml. The front label should also contain the strength of the liqueur which is 25% vol. The rear label will contain the required UK legal information such as government health warning, number of UK units of alcohol as well as the place of bottling which is Wick, Caithness, Scotland. A barcode will also be on the rear label and I have added it as a jpg file. On my current homemade label I also have the following text on the rear label: "Due to the ferocious tides, currents and winds that shape the narrow stretch of water separating Caithness from the Orkney Islands in the far North of Scotland, it has become known to generations of sailors as "Gravelstern" and is the graveyard of countless number of ships. Gravelstern Spiced Rum Liqueur aims to capture the spirit of those brave men and women who have risked all on these treacherous shores". For the main front label I am keen for the designer to explore the themes of shipwreck, sea monsters, smuggling, pistols, diving helmets, heavy seas, sea stacks, high cliffs, sealife etc. I have included a story about a local smuggler called Peter Mowbray as an example of an inspirational theme. I currently also have a website regarding Caithness shipwrecks which can be found at www.gravelstern.example and which could provide some further ideas. My feeling is that the label design should be masculine and I would like to keep away from designs that would make the label costly to print. I have included a file with my current logo but please feel free to change its colour as required and to remove the word Gravelstern from the logo if you wish. I can supply the logo file in different formats such as jpg, ai, eps, pdf, png or psd. I also have the barcode in pdf, png or svg formats. The word Gravelstern is a registered trademark.I have also attached a photograph of my liqueur in an attempt to show the colour of the finished product and the bottle style.
Updates
Colors
Designer to choose colors to be used in the design.
Look and feel
Each slider illustrates characteristics of the customer's brand and the style your logo design should communicate.

```html
<!DOCTYPE html>
<html lang="en">
<head>
<meta charset="utf-8">
<title>Gravelstern Spiced Rum Liqueur – Front Label</title>
<link rel="stylesheet" href="https://fonts.googleapis.com/css2?family=Germania+One&family=Merriweather:wght@400;700;900&display=swap">
<style>
  :root {
    --backdrop-light: #f4f4f4;
    --backdrop-dark: #d9d9d9;
    --label-light: #eeeeee;
    --label-mid: #e2e2e2;
    --label-dark: #d2d2d2;
    --ink: #262626;
    --ink-soft: #5a5a5a;
    --accent: #c4742a;
    --engraving-light: #b9b9b9;
    --engraving-mid: #8a8a8a;
    --engraving-dark: #4a4a4a;
  }
  * { margin: 0; padding: 0; box-sizing: border-box; }
  html, body {
    width: 749px;
    height: 1200px;
    overflow: hidden;
  }
  body {
    position: relative;
    background: radial-gradient(ellipse at 50% 40%, var(--backdrop-light) 0%, var(--backdrop-dark) 100%);
    font-family: "Merriweather", Georgia, serif;
    color: var(--ink);
  }
  .front-label {
    position: absolute;
    left: 34px;
    top: 287px;
    width: 681px;
    height: 626px;
    overflow: hidden;
    background: linear-gradient(90deg, var(--label-dark) 0%, var(--label-light) 30%, var(--label-mid) 70%, var(--label-dark) 100%);
  }
  .volume {
    position: absolute;
    top: 10px;
    left: 0;
    width: 100%;
    text-align: center;
    font-size: 16px;
    font-weight: 400;
    line-height: 20px;
    color: var(--ink-soft);
    letter-spacing: 0.5px;
  }
  .shore-scene {
    position: absolute;
    top: 40px;
    left: 0;
    width: 100%;
    height: 300px;
    background: linear-gradient(180deg, var(--engraving-light) 0%, var(--engraving-mid) 45%, var(--engraving-dark) 100%);
  }
  .brand-name {
    position: absolute;
    top: 296px;
    left: 0;
    width: 100%;
    text-align: center;
    font-family: "Germania One", "Merriweather", serif;
    font-size: 96px;
    font-weight: 400;
    line-height: 1;
    letter-spacing: 2px;
    color: var(--ink);
  }
  .brand-name .registered {
    font-family: "Merriweather", Georgia, serif;
    font-size: 20px;
    vertical-align: top;
    position: relative;
    top: 6px;
    margin-left: 2px;
  }
  .variant {
    position: absolute;
    top: 402px;
    left: 0;
    width: 100%;
    display: flex;
    justify-content: center;
    align-items: center;
    gap: 14px;
    font-size: 46px;
    font-weight: 700;
    line-height: 52px;
    color: var(--ink);
  }
  .variant .rule {
    width: 80px;
    height: 3px;
    background: var(--ink);
  }
  .product-type {
    position: absolute;
    top: 461px;
    left: 0;
    width: 100%;
    text-align: center;
    font-size: 46px;
    font-weight: 700;
    line-height: 52px;
    color: var(--ink);
  }
  .brand-mark {
    position: absolute;
    top: 540px;
    left: 0;
    width: 100%;
    text-align: center;
    font-size: 24px;
    font-weight: 700;
    line-height: 32px;
    color: var(--accent);
    letter-spacing: 1px;
  }
  .strength {
    position: absolute;
    top: 592px;
    left: 0;
    width: 100%;
    text-align: center;
    font-size: 16px;
    font-weight: 400;
    line-height: 20px;
    color: var(--ink-soft);
    letter-spacing: 0.5px;
  }
</style>
</head>
<body>
  <main class="front-label">
    <p class="volume">500ML</p>
    <div class="shore-scene" role="img" aria-label="Engraved illustration of sailors rolling a rum barrel along a rocky shore with the sea and a sea stack behind"></div>
    <h1 class="brand-name">GRAVELSTERN<span class="registered">®</span></h1>
    <p class="variant"><span class="rule"></span>SPICED<span class="rule"></span></p>
    <p class="product-type">RUM LIQUEUR</p>
    <p class="brand-mark">Gravelstern</p>
    <p class="strength">25% VOL</p>
  </main>
</body>
</html>
```